Smack you in the face - Landing page for Residential Electrical Repairs (Searchly Ads)

I need an effective landing page for Searchly ads. The ads will target residential electrical repairs. Lighting Outages, Power Outages, Breakers Tripping, Outlets Not Working. I need a strong call to action to Call Us Now! Forms don't work well for us so we only need one form as a last option at the bottom of the page. We only work on homes. the website is https://www.vantor-wiring.example/
email is : support@vantor-wiring.example
Phone 555-217-4086

**This is about one focused service. Electrical Repairs - That includes Partial Power Outages, Outlets Not Working, Tripped Breakers, Electrical Panel repairs, and Fusebox Repairs. The area served will only be Greenville, SC. KOBA is the platform

Target Market(s)

Homeonwers in need of electrical repair

Industry/Entity Type

Residential Electricians

Coding

Coded - Design and coding required

Requirements
Must have
• Strong to action for phone calls, this landing page must grab action fast.
Nice to have
• Social proof with existing 5 start reviews for Searchly, Rately, TCB, and Friendnet
Should not have
• Should not be form based. I do not like the site's current them, please don't copy it. Make your own.

```html
<!DOCTYPE html>
<html lang="en">
<head>
<meta charset="utf-8">
<title>Vantor Wiring – Residential Electrical Repairs in Greenville, SC</title>
<link rel="stylesheet" href="https://fonts.googleapis.com/css2?family=Oswald:wght@500;600&family=Montserrat:wght@500;600;700&family=Poppins:wght@400;500;600&display=swap">
<style>
:root{
  --blue:#2b8fc8;
  --blue-dark:#1f6fa3;
  --orange:#f26b21;
  --ink:#1c1e22;
  --text:#3a3d42;
  --muted:#6a6e74;
  --light:#f3f3f3;
  --white:#ffffff;
  --night:#15171b;
}
*{box-sizing:border-box;margin:0;padding:0}
html,body{width:1200px;height:5076px;overflow:hidden}
body{font-family:"Poppins",sans-serif;color:var(--text);background:var(--white);position:relative}
section,footer,header{position:relative;width:1200px;overflow:hidden}
.abs{position:absolute}
.btn{display:inline-block;background:var(--orange);color:var(--white);font:600 12px "Poppins",sans-serif;padding:9px 22px;border-radius:3px;text-decoration:none}
.eyebrow{font:500 12px "Poppins",sans-serif;color:var(--orange);text-align:center}
.title{font:600 32px "Montserrat",sans-serif;text-align:center;letter-spacing:.5px}
.title .a{color:var(--blue-dark)}.title .b{color:var(--blue)}
.divider{display:flex;align-items:center;justify-content:center;gap:6px;margin-top:8px}
.divider i{display:block;width:32px;height:2px;background:var(--blue)}
.divider svg{width:10px;height:14px}
.photo{background:linear-gradient(135deg,#5d6c7a,#a9b3bc 60%,#4a5561)}

/* hero */
.hero{height:750px}
.hero-bg{inset:0;background:linear-gradient(180deg,#6d8aa3 0%,#8aa1a6 35%,#5f7357 70%,#3f5238 100%)}
.hero-shade{inset:0;background:linear-gradient(90deg,rgba(0,0,0,.45),rgba(0,0,0,.05) 70%)}
.hero-curve{left:0;bottom:0;width:1200px;height:750px}
.logo{font:700 22px "Montserrat",sans-serif;letter-spacing:2px;display:flex;align-items:center;gap:8px;white-space:nowrap}
.logo .dot{width:14px;height:14px;border-radius:50%;background:var(--orange);flex:none}
.hero .logo{left:142px;top:56px;color:var(--white)}
.hero .top-btn{left:728px;top:52px}
.hero .phone{left:876px;top:46px;display:flex;align-items:center;gap:12px;color:var(--white)}
.phone .ico{width:38px;height:38px;border-radius:50%;background:var(--white);display:flex;align-items:center;justify-content:center}
.phone small{display:block;font-size:14px}
.phone b{font:500 16px "Poppins",sans-serif}
.hero h1{left:142px;top:240px;width:540px;color:var(--white);font:600 40px/50px "Oswald",sans-serif}
.hero .lead{left:142px;top:344px;width:500px;color:var(--white);font:500 15px/28px "Oswald",sans-serif}
.hero .cta{left:142px;top:410px}
.badge{left:796px;top:460px;width:284px;height:284px;border-radius:50%;border:8px solid var(--blue)}
.badge .photo{position:absolute;inset:0;border-radius:50%;background:linear-gradient(160deg,#7ea5c8,#3b5d86 60%,#2b3f5c)}
.badge .num{position:absolute;left:0;right:0;top:80px;text-align:center;color:var(--white);font:600 56px/1 "Montserrat",sans-serif}
.badge .lbl{position:absolute;left:0;right:0;top:142px;text-align:center;color:var(--white);font:600 19px/26px "Montserrat",sans-serif}

/* gallery */
.gallery{height:610px}
.gallery .head{left:0;right:0;top:80px}
.grid{left:142px;top:175px;width:916px;height:337px}
.grid .photo{position:absolute}

/* services */
.services{height:600px}
.services-bg{inset:0;background:linear-gradient(120deg,#1f79b1,#3599cf 55%,#2a86bf)}
.services-top{left:0;top:0;width:1200px;height:60px}
.services .head{left:0;right:0;top:70px}
.services .eyebrow{color:var(--white)}
.services .title{color:var(--white)}
.services .divider i{background:var(--white)}
.card{top:153px;width:217px;height:353px;background:var(--white);border-radius:110px 110px 0 0;text-align:center;padding:25px 18px 0}
.card .photo{width:158px;height:158px;border-radius:50%;margin:0 auto}
.card h3{font:600 14px "Poppins",sans-serif;color:var(--ink);margin:20px 0 8px}
.card p{font:400 11.5px/23px "Poppins",sans-serif;color:var(--text)}

/* cta strip */
.cta-strip{height:265px;text-align:center}
.cta-strip h2{position:absolute;left:0;right:0;top:64px;font:600 25px/34px "Montserrat",sans-serif;color:var(--ink)}
.cta-strip p{position:absolute;left:0;right:0;top:138px;font:500 15px "Poppins",sans-serif;color:var(--ink)}
.cta-strip .btn{position:absolute;left:536px;top:176px}

/* about */
.about{height:552px;background:var(--light)}
.about .big{left:188px;top:92px;width:338px;height:338px;border-radius:50%;border:5px solid var(--blue);background:linear-gradient(150deg,#6d8fb0,#3e6890 55%,#7f93a6)}
.about .small{left:140px;top:312px;width:148px;height:148px;border-radius:50%;border:4px solid var(--orange);background:linear-gradient(150deg,#d7dde2,#8b9bab)}
.about .copy{left:558px;top:80px;width:500px}
.about .eyebrow{text-align:left}
.about h2{font:700 32px "Montserrat",sans-serif;color:var(--blue);margin-top:4px}
.about .divider{justify-content:flex-start}
.about p{font:400 11.5px/23px "Poppins",sans-serif;color:var(--text);margin-top:12px}
.about .btn{margin-top:20px}

/* why choose */
.why{height:790px;background:var(--night)}
.why-bg{inset:0;background:linear-gradient(180deg,#2a3140,#1e2430 60%,#171a20)}
.why-bottom{left:0;bottom:0;width:1200px;height:110px}
.why .eyebrow{left:0;right:0;top:135px;color:var(--white);font-size:11px;position:absolute}
.why h2{left:0;right:0;top:155px;text-align:center;color:var(--white);font:600 32px "Montserrat",sans-serif;letter-spacing:.5px}
.why .intro{left:340px;width:520px;top:215px;text-align:center;color:var(--white);font:400 12px/24px "Poppins",sans-serif}
.why .rings{left:0;top:0;width:1200px;height:790px}
.hub{left:457px;top:310px;width:268px;height:268px;border-radius:50%;background:var(--white);display:flex;align-items:center;justify-content:center}
.hub .logo{color:var(--ink);font-size:20px;letter-spacing:1.5px}
.reason{color:var(--white);font:500 11.5px/20px "Poppins",sans-serif;text-transform:uppercase}
.reason.l{text-align:right;width:220px}
.icon-ring{width:76px;height:76px;border-radius:50%;background:var(--white);display:flex;align-items:center;justify-content:center}
.icon-ring svg{width:38px;height:38px}
.why .btn{left:536px;top:635px}

/* reviews */
.reviews{height:592px}
.reviews .head{left:0;right:0;top:70px}
.reviews .title .a,.reviews .title .b{color:var(--blue)}
.sources{left:0;right:0;top:180px;display:flex;justify-content:center;gap:34px}
.source{display:flex;align-items:center;gap:6px;font:600 17px "Poppins",sans-serif;color:var(--ink)}
.source .mark{width:14px;height:14px;border-radius:50%;background:var(--blue)}
.source .mark.sq{border-radius:2px;background:var(--orange)}
.source .stars{display:block;font-size:10px;color:#f5a623;letter-spacing:1px}
.review{top:272px;width:370px;height:250px;background:var(--white);box-shadow:0 4px 18px rgba(0,0,0,.1);border-bottom:5px solid var(--blue);text-align:center;padding:95px 20px 0}
.review .avatar{position:absolute;left:147px;top:-22px;width:76px;height:76px;border-radius:50%;border:3px solid var(--blue);background:linear-gradient(160deg,#c9a88a,#6d5847)}
.review .src{position:absolute;right:22px;top:18px;width:24px;height:24px;border-radius:50%;background:#e8ecef}
.review h4{position:absolute;left:0;right:0;top:66px;font:500 17px "Poppins",sans-serif;color:var(--ink)}
.review p{font:400 11px/22px "Poppins",sans-serif;color:var(--text)}
.arrow{top:385px;width:22px;height:22px;border-radius:50%;background:var(--white);box-shadow:0 2px 6px rgba(0,0,0,.15);display:flex;align-items:center;justify-content:center}

/* contact */
.contact{height:522px}
.contact-bg{inset:0;background:linear-gradient(120deg,#2380bb,#3a9ed3 50%,#1f72a8)}
.contact .eyebrow{position:absolute;left:0;right:0;top:84px;color:var(--white);font-size:11px}
.contact h2{left:0;right:0;top:100px;text-align:center;color:var(--white);font:500 32px "Montserrat",sans-serif;letter-spacing:1px}
.contact .divider{position:absolute;left:0;right:0;top:142px}
.contact .divider i{background:var(--white)}
.field{background:var(--white);height:38px;border-radius:2px;display:flex;align-items:center;gap:10px;padding:0 16px;font:400 12px "Poppins",sans-serif;color:#6b6f75}
.field svg{width:13px;height:13px}
.field.msg{align-items:flex-start;padding-top:14px;height:94px}
.contact .btn{left:536px;top:394px;width:126px;text-align:center;padding:10px 0}

/* footer */
footer{height:358px;background:var(--night)}
footer .logo{left:142px;top:148px;color:var(--white);font-size:30px}
.fcol h5{font:600 12px "Montserrat",sans-serif;color:var(--blue)}
.fcol .divider{justify-content:flex-start;gap:4px;margin-top:6px}
.fcol .divider i{width:20px}
.frow{display:flex;gap:12px;align-items:flex-start;margin-top:18px;color:var(--white);font:400 11px/17px "Poppins",sans-serif}
.frow svg{width:26px;height:26px;flex:none}
.social{display:flex;align-items:center;gap:10px;margin-top:18px;color:var(--white);font:400 11px "Poppins",sans-serif}
.social span{width:22px;height:22px;border:1px solid var(--white);border-radius:50%}
.legal{left:0;bottom:0;width:1200px;height:42px;background:var(--orange);color:var(--white);font:400 11.5px "Poppins",sans-serif;display:flex;align-items:center;justify-content:center}
</style>
</head>
<body>

<header class="hero">
  <div class="abs hero-bg" role="img" aria-label="Aerial photo of the Greenville skyline and tree-lined streets"></div>
  <div class="abs hero-shade"></div>
  <svg class="abs hero-curve" viewBox="0 0 1200 750" preserveAspectRatio="none" aria-hidden="true">
    <path d="M0 520 Q360 820 1200 330 L1200 750 L0 750Z" fill="#f26b21"/>
    <path d="M0 560 Q380 830 1200 420 L1200 750 L0 750Z" fill="#ffffff"/>
  </svg>
  <div class="abs logo"><span class="dot"></span>VANTOR WIRING</div>
  <a class="abs btn top-btn" href="tel:5552174086">Call Us Now!</a>
  <div class="abs phone">
    <span class="ico"><svg width="18" height="18" viewBox="0 0 24 24"><path d="M6.6 10.8a15.1 15.1 0 0 0 6.6 6.6l2.2-2.2a1 1 0 0 1 1-.25 11.4 11.4 0 0 0 3.6.57 1 1 0 0 1 1 1V20a1 1 0 0 1-1 1A17 17 0 0 1 3 4a1 1 0 0 1 1-1h3.5a1 1 0 0 1 1 1c0 1.25.2 2.45.57 3.57a1 1 0 0 1-.25 1z" fill="#2b8fc8"/></svg></span>
    <div><small>Phone</small><b>555-217-4086</b></div>
  </div>
  <h1 class="abs">Make Us Your First Choice For Electrical Services</h1>
  <p class="abs lead">Licensed Electricians In Greenville, SC Ensuring Top-tier Service For Every Call.</p>
  <a class="abs btn cta" href="tel:5552174086">Call Us Now!</a>
  <div class="abs badge">
    <div class="photo" role="img" aria-label="Photo of two electricians in blue uniforms"></div>
    <div class="num">8+</div>
    <div class="lbl">Years Of<br>Experience</div>
  </div>
</header>

<section class="gallery">
  <div class="abs head">
    <p class="eyebrow">Portfolio</p>
    <h2 class="title"><span class="a">WORK</span> <span class="b">GALLERY</span></h2>
    <div class="divider"><i></i><svg viewBox="0 0 10 14"><path d="M6 0 1 8h3l-1 6 6-9H6z" fill="#2b8fc8"/></svg><i></i></div>
  </div>
  <div class="abs grid">
    <div class="photo" style="left:0;top:0;width:458px;height:337px" role="img" aria-label="Electrician in a white hard hat working on a breaker panel"></div>
    <div class="photo" style="left:466px;top:0;width:221px;height:164px" role="img" aria-label="Electrician inspecting a wall-mounted meter"></div>
    <div class="photo" style="left:695px;top:0;width:221px;height:164px" role="img" aria-label="Hands wiring an outlet box"></div>
    <div class="photo" style="left:466px;top:172px;width:221px;height:165px" role="img" aria-label="Close-up of circuit breaker wiring"></div>
    <div class="photo" style="left:695px;top:172px;width:221px;height:165px" role="img" aria-label="Hand switching a breaker in a panel"></div>
  </div>
</section>

<section class="services">
  <div class="abs services-bg" role="img" aria-label="Blue-tinted photo of an electrician at work"></div>
  <svg class="abs services-top" viewBox="0 0 1200 60" preserveAspectRatio="none" aria-hidden="true"><path d="M0 0H1200V0Q600 70 0 40Z" fill="#ffffff"/></svg>
  <div class="abs head">
    <p class="eyebrow">Our Services</p>
    <h2 class="title">WHAT WE DO</h2>
    <div class="divider"><i></i><svg viewBox="0 0 10 14"><path d="M6 0 1 8h3l-1 6 6-9H6z" fill="#fff"/></svg><i></i></div>
  </div>
  <div class="abs card" style="left:142px">
    <div class="photo" role="img" aria-label="Hand testing a breaker"></div>
    <h3>Partial Power Outages</h3>
    <p>Prolonged darkness or interrupted power supply can disrupt your routine. We ensure that your power is restored swiftly.</p>
  </div>
  <div class="abs card" style="left:374px">
    <div class="photo" role="img" aria-label="Multimeter testing an outlet"></div>
    <h3>Outlets Not Working</h3>
    <p>As foundational elements of any residential or commercial property, outlets and switches are easy to overlook—until they stop...</p>
  </div>
  <div class="abs card" style="left:607px">
    <div class="photo" role="img" aria-label="Electrician repairing a panel"></div>
    <h3>Electrical Panel Repairs</h3>
    <p>From minor glitches to significant malfunctions, we're adept at diagnosing &amp; resolving all electrical panel issues.</p>
  </div>
  <div class="abs card" style="left:839px">
    <div class="photo" role="img" aria-label="Electrician in a hard hat at a fuse box"></div>
    <h3>Fusebox Repairs</h3>
    <p>Protect your electrical system with our expert fuse box repair services. Lorem ipsum dolor sit consectetur adipiscing elit.</p>
  </div>
</section>

<section class="cta-strip">
  <h2>Try Our Services Once And You Won't Need To Go<br>Anywhere Else</h2>
  <p>Expert Solutions And Excellent Service</p>
  <a class="btn" href="tel:5552174086">Call Us Now!</a>
</section>

<section class="about">
  <div class="abs big" role="img" aria-label="Smiling electrician in a cap working at a panel"></div>
  <div class="abs small" role="img" aria-label="Two electricians in hard hats"></div>
  <div class="abs copy">
    <p class="eyebrow">ABOUT</p>
    <h2>VANTOR WIRING</h2>
    <div class="divider"><svg viewBox="0 0 10 14"><path d="M6 0 1 8h3l-1 6 6-9H6z" fill="#2b8fc8"/></svg><i style="width:20px"></i></div>
    <p>At Vantor Wiring, EV Chargers, &amp; Generators, your electrical emergency is our urgency. We have Licensed Electricians in Greenville, SC, Raleigh, NC, and Charlotte, NC, ensuring top-tier service for every call. We've built our reputation as the go-to Emergency Electrician for homeowners in need. When you find yourself thinking about an "electrician near me," think of us. While many electrical contractors chase after large-scale construction and commercial building projects, we prioritize you – the homeowner.</p>
    <p>We're committed to delivering unbeatable same-day service for all your residential electrical repairs, EV chargers &amp; Generator installations. With us, you're not just another job; you're our top priority. Choose Vantor Wiring for swift, safe, &amp; standout electrical solutions.</p>
    <a class="btn" href="tel:5552174086">Call Us Now!</a>
  </div>
</section>

<section class="why">
  <div class="abs why-bg" role="img" aria-label="Dark team photo of the crew in front of a service van"></div>
  <svg class="abs why-bottom" viewBox="0 0 1200 110" preserveAspectRatio="none" aria-hidden="true"><path d="M0 10Q600 130 1200 10V110H0Z" fill="#ffffff"/></svg>
  <p class="eyebrow">WHY CHOOSE US</p>
  <h2 class="abs">GREAT REASONS TO VANTOR WIRING</h2>
  <p class="abs intro">Lorem ipsum dolor sit amet, consectetur adipiscing elit, sed do eiusmod tempor incididunt ut labore et dolore magna aliqua.</p>
  <svg class="abs rings" viewBox="0 0 1200 790" aria-hidden="true">
    <path d="M414 325 A200 200 0 0 0 414 571" fill="none" stroke="#fff" stroke-width="2"/>
    <path d="M782 325 A200 200 0 0 1 782 571" fill="none" stroke="#fff" stroke-width="2"/>
  </svg>
  <div class="abs hub"><div class="logo"><span class="dot"></span>VANTOR WIRING</div></div>

  <div class="abs icon-ring" style="left:376px;top:287px"><svg viewBox="0 0 24 24" fill="none" stroke="#f26b21" stroke-width="1.5"><rect x="5" y="3" width="14" height="18" rx="1"/><circle cx="12" cy="10" r="3"/><path d="M9 16h6"/></svg></div>
  <div class="abs icon-ring" style="left:336px;top:411px"><svg viewBox="0 0 24 24" fill="none" stroke="#f26b21" stroke-width="1.5"><rect x="4" y="3" width="13" height="18" rx="1"/><path d="M7 8h7M7 12h7M7 16h4"/><path d="m14 18 2 2 4-5"/></svg></div>
  <div class="abs icon-ring" style="left:376px;top:533px"><svg viewBox="0 0 24 24" fill="none" stroke="#f26b21" stroke-width="1.5"><circle cx="12" cy="10" r="6"/><path d="M12 7v6M10 8.5h3a1.5 1.5 0 0 1 0 3h-2a1.5 1.5 0 0 0 0 3h3M9 16l-2 6 5-2 5 2-2-6"/></svg></div>
  <div class="abs icon-ring" style="left:744px;top:287px"><svg viewBox="0 0 24 24" fill="none" stroke="#f26b21" stroke-width="1.5"><rect x="6" y="3" width="13" height="18" rx="1"/><path d="M9 8h7M9 12h7M9 16h4"/><path d="M3 9h3M3 13h3"/></svg></div>
  <div class="abs icon-ring" style="left:770px;top:411px"><svg viewBox="0 0 24 24" fill="none" stroke="#f26b21" stroke-width="1.5"><path d="M20 12a8 8 0 1 1-3-6.2"/><path d="M17 3v3h-3"/><text x="7.5" y="15" font-size="7" fill="#f26b21" stroke="none" font-family="Poppins,sans-serif">24</text></svg></div>
  <div class="abs icon-ring" style="left:734px;top:533px"><svg viewBox="0 0 24 24" fill="none" stroke="#f26b21" stroke-width="1.5"><path d="M2 15h4l4 2h4a1.5 1.5 0 0 0 0-3h-3M6 20l5 1 10-5a1.5 1.5 0 0 0-2-2l-5 2"/><path d="m14 4 1 2 2 .3-1.5 1.4.4 2.1-1.9-1-1.9 1 .4-2.1L11 6.3l2-.3z"/></svg></div>

  <p class="abs reason l" style="left:144px;top:305px">Our owner has a<br>decade of experience</p>
  <p class="abs reason l" style="left:104px;top:429px">Fully licensed<br>and insured</p>
  <p class="abs reason l" style="left:144px;top:551px">Cost effective<br>solutions</p>
  <p class="abs reason" style="left:828px;top:305px">We offer<br>free estimates</p>
  <p class="abs reason" style="left:864px;top:429px">Same day<br>service available</p>
  <p class="abs reason" style="left:826px;top:551px">Exceptional<br>customer service</p>
  <a class="abs btn" href="tel:5552174086">Call Us Now!</a>
</section>

<section class="reviews">
  <div class="abs head">
    <p class="eyebrow">TESTIMONIALS</p>
    <h2 class="title"><span class="a">CUSTOMER</span> <span class="b">REVIEWS</span></h2>
    <div class="divider"><i></i><svg viewBox="0 0 10 14"><path d="M6 0 1 8h3l-1 6 6-9H6z" fill="#2b8fc8"/></svg><i></i></div>
  </div>
  <div class="abs sources">
    <div class="source"><span class="mark"></span><div>Searchly<span class="stars">★★★★★</span></div></div>
    <div class="source"><span class="mark sq"></span><div>Rately<span class="stars">★★★★★</span></div></div>
    <div class="source"><span class="mark sq" style="background:#1f6fa3"></span><div>TCB<span class="stars">★★★★★</span></div></div>
    <div class="source"><span class="mark sq" style="background:#2b8fc8"></span><div>Friendnet<span class="stars">★★★★★</span></div></div>
  </div>
  <div class="abs arrow" style="left:178px"><svg width="8" height="10" viewBox="0 0 8 10"><path d="M6 1 2 5l4 4" fill="none" stroke="#f26b21" stroke-width="2"/></svg></div>
  <div class="abs arrow" style="left:1000px"><svg width="8" height="10" viewBox="0 0 8 10"><path d="m2 1 4 4-4 4" fill="none" stroke="#f26b21" stroke-width="2"/></svg></div>
  <div class="abs review" style="left:187px">
    <div class="avatar" role="img" aria-label="Reviewer portrait"></div>
    <span class="src"></span>
    <h4>Dana Whitfield</h4>
    <p>Searched online to find an electrician and MARCO from Foothill Electric responded. He was very friendly, professional and showed interest in my dilemma. He made it easy to talk to and help me understand the urgency of my situation. He not only solved the issue...</p>
  </div>
  <div class="abs review" style="left:624px">
    <div class="avatar" role="img" aria-label="Reviewer portrait"></div>
    <span class="src" style="background:#fde2d3"></span>
    <h4>Karina Lowell</h4>
    <p>Theo was wonderful and immediately identified what was tripping an electrical breaker box out by our pool. He then installed an electrical outlet for me that I requested in the attic; both jobs done very well in about an hours time. Thank you Theo! Will definitely...</p>
  </div>
</section>

<section class="contact">
  <div class="abs contact-bg" role="img" aria-label="Blue-tinted photo of an electrician at a panel"></div>
  <p class="eyebrow">CONTACT US</p>
  <h2 class="abs">GET IN TOUCH</h2>
  <div class="divider"><i></i><svg viewBox="0 0 10 14"><path d="M6 0 1 8h3l-1 6 6-9H6z" fill="#fff"/></svg><i></i></div>
  <div class="abs field" style="left:345px;top:166px;width:246px"><svg viewBox="0 0 24 24"><circle cx="12" cy="8" r="5" fill="#2b8fc8"/><path d="M3 22a9 9 0 0 1 18 0z" fill="#2b8fc8"/></svg>First Name</div>
  <div class="abs field" style="left:607px;top:166px;width:246px"><svg viewBox="0 0 24 24"><circle cx="12" cy="8" r="5" fill="#2b8fc8"/><path d="M3 22a9 9 0 0 1 18 0z" fill="#2b8fc8"/></svg>Last Name</div>
  <div class="abs field" style="left:345px;top:221px;width:246px"><svg viewBox="0 0 24 24"><path d="M6.6 10.8a15.1 15.1 0 0 0 6.6 6.6l2.2-2.2a1 1 0 0 1 1-.25 11.4 11.4 0 0 0 3.6.57 1 1 0 0 1 1 1V20a1 1 0 0 1-1 1A17 17 0 0 1 3 4a1 1 0 0 1 1-1h3.5a1 1 0 0 1 1 1c0 1.25.2 2.45.57 3.57a1 1 0 0 1-.25 1z" fill="#2b8fc8"/></svg>Phone Number</div>
  <div class="abs field" style="left:607px;top:221px;width:246px"><svg viewBox="0 0 24 24"><rect x="2" y="5" width="20" height="14" rx="1" fill="#2b8fc8"/><path d="m2 6 10 7 10-7" fill="none" stroke="#fff" stroke-width="1.5"/></svg>Email Address</div>
  <div class="abs field msg" style="left:345px;top:280px;width:508px"><svg viewBox="0 0 24 24"><rect x="2" y="5" width="20" height="14" rx="1" fill="#2b8fc8"/><path d="m2 6 10 7 10-7" fill="none" stroke="#fff" stroke-width="1.5"/></svg>Message</div>
  <a class="abs btn" href="#">Submit</a>
</section>

<footer>
  <div class="abs logo"><span class="dot"></span>VANTOR WIRING</div>
  <div class="abs fcol" style="left:558px;top:68px;width:360px">
    <h5>CONTACT DETAILS</h5>
    <div class="divider"><svg viewBox="0 0 10 14"><path d="M6 0 1 8h3l-1 6 6-9H6z" fill="#2b8fc8"/></svg><i></i></div>
    <div class="frow"><svg viewBox="0 0 24 24" fill="none" stroke="#fff" stroke-width="1.3"><circle cx="12" cy="12" r="10"/><path d="M2 12h20M12 2c3 3 3 17 0 20M12 2c-3 3-3 17 0 20"/></svg><span>482 Meadowlark Rd Suite 210<br>Greenville, SC 29601</span></div>
    <div class="frow"><svg viewBox="0 0 24 24" fill="none" stroke="#fff" stroke-width="1.3"><path d="M6.6 10.8a15.1 15.1 0 0 0 6.6 6.6l2.2-2.2a1 1 0 0 1 1-.25 11.4 11.4 0 0 0 3.6.57 1 1 0 0 1 1 1V20a1 1 0 0 1-1 1A17 17 0 0 1 3 4a1 1 0 0 1 1-1h3.5a1 1 0 0 1 1 1c0 1.25.2 2.45.57 3.57a1 1 0 0 1-.25 1z"/></svg><span>PHONE<br>555-217-4086</span></div>
    <div class="frow"><svg viewBox="0 0 24 24" fill="none" stroke="#fff" stroke-width="1.3"><rect x="2" y="5" width="20" height="14" rx="1"/><path d="m2 6 10 7 10-7"/></svg><span>EMAIL<br>support@vantor-wiring.example</span></div>
  </div>
  <div class="abs fcol" style="left:963px;top:68px;width:150px">
    <h5>FOLLOW US</h5>
    <div class="divider"><svg viewBox="0 0 10 14"><path d="M6 0 1 8h3l-1 6 6-9H6z" fill="#2b8fc8"/></svg><i></i></div>
    <div class="social"><span></span>Friendnet</div>
    <div class="social"><span></span>Chirper</div>
    <div class="social"><span></span>Linkwork</div>
    <div class="social"><span></span>Snapgram</div>
  </div>
  <div class="abs legal">© 2023 Vantor Wiring. All Rights Reserved.</div>
</footer>

</body>
</html>
```